Call Center In Need of Website Design

We are a call center that provides inbound and outbound calling & marketing services for eCommerce store. We would like to see a fun, creative, playful design that is simple.

Here are some sample design sites we like;
- https://www.velmoreline.com/
- https://pindrask.io/
- https://www.glimbertic.com/live-chat-software/
- https://www.zavrolin.com/

Here are some competitor sites;
- https://www.ostrevaglinks.com/
- https://www.helpkestrel.com/

I have attached website content for your use.

Target Market(s)

eCommerce

Coding

Coded - Design and coding required

Number of Pages Required

5+ page

Font styles to use
Sans Serif

Colors

Designer to choose colors to be used in the design.

Requirements
Must have
• Must have designs for the following 5 separate pages;
• 1. Home (landing)
• - This will be were the design style really needs to show.
• - Just needs to touch on key services
• - CTA
• 2. About Us
• - Basic page for about me paragraph
• 3. Services
• - List of services with icons
• - Click on service type to expand details or hover over service icon to view popup bubble with details about that service
• 4. Pricing
• - Option to bundle 1(one) digital service plan and 1(one) call center service plan
• - Bundling adds 10% monthly discount to over all price
• - Customer does NOT have to bundle
• - FAQ
• 5. Contact Us
• - Include a capture form (name, company name, email, phone, message)
• - Contact info
• - Business hours
• When customer purchases their desired plan, then they are taken to a page where they must schedule a call with an account rep.
Nice to have
• home page animations
Should not have
• All information on Home/Landing page.

```html
<!DOCTYPE html>
<html lang="en">
<head>
<meta charset="utf-8">
<title>Plumora — Digital &amp; Call Center Services</title>
<link rel="stylesheet" href="https://fonts.googleapis.com/css2?family=Montserrat:wght@400;500&family=Open+Sans:wght@400&display=swap">
<style>
:root{
  --teal:#76c8b1;
  --teal-dark:#5aa891;
  --teal-btn:#5e9e8c;
  --charcoal:#414a48;
  --charcoal-btn:#2c3231;
  --ink:#1d1f20;
  --text:#444;
  --footer-bg:#f3f7f6;
  --footer-line:#dfe6e4;
  --white:#fff;
}
*{margin:0;padding:0;box-sizing:border-box}
html,body{width:977px;height:1200px;overflow:hidden;background:var(--white)}
body{position:relative;font-family:'Montserrat',sans-serif;color:var(--ink)}
.site-header{position:absolute;top:0;left:0;width:977px;height:70px;background:var(--white);box-shadow:0 2px 4px rgba(0,0,0,.06);z-index:3}
.brand{position:absolute;left:148px;top:19px;display:flex;align-items:center;gap:10px}
.brand-dot{width:30px;height:30px;border-radius:50%;border:3px solid var(--teal)}
.brand-name{font-size:20px;font-weight:400;letter-spacing:3px;color:#4a4f50}
.main-nav{position:absolute;top:31px;left:412px;display:flex;gap:0}
.main-nav a{font-size:12px;color:var(--ink);text-decoration:none;margin-right:32px}
.main-nav a.active{color:var(--teal)}
.hero{position:absolute;top:70px;left:0;width:977px;height:490px;overflow:hidden}
.hero-photo{position:absolute;inset:0;background:linear-gradient(100deg,#f2f0ec 0%,#e9e6df 35%,#d9cfc3 55%,#c6c9cc 75%,#aeb8c2 100%)}
.hero-curve{position:absolute;left:0;bottom:0;width:977px;height:90px}
.hero-copy{position:absolute;left:148px;top:110px}
.hero-title{font-size:25px;font-weight:400;line-height:34px;color:var(--ink)}
.hero-title span{display:block;color:var(--teal)}
.hero-text{font-family:'Open Sans',sans-serif;font-size:13px;line-height:20px;color:var(--text);margin-top:14px;width:290px}
.btn{display:inline-block;border-radius:16px;font-size:11px;color:var(--white);text-decoration:none;text-align:center;height:32px;line-height:32px;width:108px}
.hero .btn{background:var(--teal);margin-top:20px;margin-left:-3px}
.slider-dots{position:absolute;top:381px;left:456px;display:flex;gap:7px}
.slider-dots i{width:10px;height:10px;border-radius:50%;background:var(--white)}
.slider-dots i.current{background:transparent;border:2px solid var(--white)}
.welcome{position:absolute;top:542px;left:0;width:977px;text-align:center}
.welcome h2{font-size:21px;font-weight:500;letter-spacing:.3px}
.welcome p{font-family:'Open Sans',sans-serif;font-size:13px;line-height:20px;color:var(--text);width:590px;margin:12px auto 0}
.service-card{position:absolute;top:747px;width:295px;height:286px;border-radius:3px;text-align:center;color:var(--white);box-shadow:0 2px 4px rgba(0,0,0,.12)}
.service-card.digital{left:185px;background:var(--teal)}
.service-card.call{left:505px;background:var(--charcoal)}
.card-icon{position:absolute;left:50%;top:-36px;width:84px;height:84px;margin-left:-42px;border-radius:50%;background:var(--teal);border:4px solid var(--white);box-shadow:0 2px 4px rgba(0,0,0,.15);display:flex;align-items:center;justify-content:center}
.call .card-icon{top:-29px}
.service-card h3{font-size:16px;font-weight:400;margin-top:64px}
.service-card ul{list-style:none;margin-top:11px}
.service-card li{font-size:10px;line-height:21px}
.service-card li::before{content:"›";font-weight:500;font-size:14px;margin-right:4px}
.service-card .btn{position:absolute;left:94px;top:234px}
.digital .btn{background:var(--teal-btn)}
.call .btn{background:var(--charcoal-btn)}
.site-footer{position:absolute;top:1097px;left:0;width:977px;height:103px;background:var(--footer-bg);border-top:2px solid var(--footer-line)}
.footer-nav{position:absolute;left:157px;top:36px;display:flex}
.footer-nav a{font-size:10px;color:var(--ink);text-decoration:none;margin-right:29px}
.copyright{position:absolute;left:157px;top:60px;font-size:8px;color:#333}
.social{position:absolute;left:716px;top:44px;display:flex;gap:4px}
.social a{width:24px;height:24px;border-radius:50%;border:1px solid var(--teal)}
</style>
</head>
<body>
<header class="site-header">
  <div class="brand"><span class="brand-dot"></span><span class="brand-name">PLUMORA</span></div>
  <nav class="main-nav">
    <a href="#" class="active">HOME</a><a href="#">ABOUT US</a><a href="#">SERVICES</a><a href="#">PRICING</a><a href="#">CONTACT US</a>
  </nav>
</header>

<section class="hero">
  <div class="hero-photo" role="img" aria-label="Photo of a smiling call center agent wearing a headset, with a colleague working on a laptop in the background"></div>
  <div class="hero-copy">
    <h1 class="hero-title">DIGITAL &amp; CALL CENTER<span>SERVICES EXPERT</span></h1>
    <p class="hero-text">Curabitur iaculis tempus eros Curabitur vel mi sit amet magna malesuada ultrices</p>
    <a href="#" class="btn">Learn More</a>
  </div>
  <div class="slider-dots"><i class="current"></i><i></i><i></i><i></i></div>
  <svg class="hero-curve" viewBox="0 0 977 90" preserveAspectRatio="none"><path d="M0 90 Q488 -70 977 90 Z" fill="#fff"/></svg>
</section>

<section class="welcome">
  <h2>WELCOME TO PLUMORA</h2>
  <p>Plumora is an omnichannel provider for customer care and back-end office support. We primarily work with eCommerce companies around the world. Our service is vital to the core operations and functionality of consumer-focused online eCommerce companies.</p>
</section>

<article class="service-card digital">
  <div class="card-icon">
    <svg width="46" height="40" viewBox="0 0 46 40" fill="none" stroke="#fff" stroke-width="1.6"><rect x="7" y="8" width="32" height="22" rx="1"/><path d="M2 32h42v3H2z"/><path d="M12 14h8v10h-8zM20 16l10-5v16l-10-5"/><path d="M24 31h-2"/></svg>
  </div>
  <h3>Digital Services</h3>
  <ul><li>Email Support</li><li>Live Chat Support</li><li>Product Research</li><li>Product Listing</li><li>Price Monitoring</li><li>Product Photo &amp; Video Editing</li></ul>
  <a href="#" class="btn">Learn More</a>
</article>

<article class="service-card call">
  <div class="card-icon">
    <svg width="40" height="44" viewBox="0 0 40 44" fill="none" stroke="#fff" stroke-width="1.6"><path d="M7 24V18a13 13 0 0 1 26 0v6"/><rect x="4" y="22" width="6" height="11" rx="2"/><rect x="30" y="22" width="6" height="11" rx="2"/><path d="M33 33v3a5 5 0 0 1-5 5h-6"/><circle cx="20" cy="41" r="2"/></svg>
  </div>
  <h3>Call Center Services</h3>
  <ul><li>Answering service</li><li>Welcome Calls</li><li>Follow-Up Service</li><li>Customer Upselling</li><li>Over-The-Phone Order Taking</li><li>Order Return Processing</li></ul>
  <a href="#" class="btn">Learn More</a>
</article>

<footer class="site-footer">
  <nav class="footer-nav"><a href="#">HOME</a><a href="#">ABOUT US</a><a href="#">SERVICES</a><a href="#">PRICING</a><a href="#">CONTACT US</a></nav>
  <p class="copyright">© 2018 Company Name &nbsp;All right reserved</p>
  <div class="social"><a href="#" aria-label="Social link 1"></a><a href="#" aria-label="Social link 2"></a><a href="#" aria-label="Social link 3"></a><a href="#" aria-label="Social link 4"></a></div>
</footer>
</body>
</html>
```